UI/UX Re-Do for TallyNest - a free to use project management platform for desktop and mobile.

UI/UX Re-Do for TallyNest
TallyNest is a free to use project management platform for desktop and mobile.
We are looking for help with our UI/UX re-design.
As of now the platform is totally functional.
The problem is around flow and look. We want TN to become something that any one can use to manage and even socialize any project. A project can be something work related like organizing a team around a software build, marketing campaign, shared client file space, etc... In fact, most of our current members are using TN for just such work projects.
We also see a project as planning a wedding, organizing a group trip, a simple to-do list, organizing a kids sports team, and so on...
To become a platform that people will use in their work and personal life we first need to become more intuitive and friendly - while maintaining advanced functionality for more advanced needs.
We need help to beautify, streamline, and simplify - while keeping all the functions.
The quickest way to understand TN, and our current issues is this short video:
https://vidlumo.example/w/Qa7KdP2mXzR
For sure see this link for the entire most recent description AND images:
https://tallynestapp.example/?p=HumbZ4KcWrT
The best way to understand TN is to actually use it:
https://tallynestapp.example
Should you choose to take a run at improving TN here are the details:
Please focus your ideas for mobile, it's where we have the biggest issues.
Feel free to get outside the box.
Avoid swipe oriented designs.
Feel free to focus on ideas over polished outputs.
Use any tool you like, PS, hand drawing, written description if you think that works best.
(FYI - we use mostly use Orvane Slides docs internally)
Point is illustration of ideas over tool choice.
Feel free to:
Create something totally new
And/or riff on what we have now
And/or riff on the new design we are considering (see images below)
|||
If we go the direction of the images/designs below the idea is to give people options on how they see/experience TN.
Just below is what we are calling Ground View. This is a more basic and simple flow. Probably a default to keep new users feeling comfortable at the start.
<img src="https://i.picbarn.example/8wNtLQe.jpg" style="width: 100%;">
https://i.picbarn.example/8wNtLQe.jpg
|||
We are calling this optional view Sky View. It is more advanced and can show all project, goal(renamed 'milestones') at the same time. This is more of a paint job on the current design.
<img src="https://i.picbarn.example/vhRmJxd.jpg" style="width: 100%;">
https://i.picbarn.example/vhRmJxd.jpg
|||
If you're submitting please let us know if you can also do the PS files for dev.
Not required, but once we nail down the concepts we want someone to hone in the PS files.
As an optional bonus we will also be giving credit to you/your company in TN.
Let us know if you do or don't want that.
We are excited to see your work!!
<img src=" " style="width: 100%;">
Target Market(s)
Anyone who needs to organize any project, big or small. The key is to make a super friendly user experience for new users while retaining advanced functions.
Industry/Entity Type
Management
Number of Pages Required
2 page

```html
<!DOCTYPE html>
<html lang="en">
<head>
<meta charset="utf-8">
<title>TallyNest – Current Shared Project</title>
<link href="https://fonts.googleapis.com/css2?family=Mulish:wght@400;500;600&display=swap" rel="stylesheet">
<style>
:root{
  --header:#3a3a3a;
  --footer:#3a3a3a;
  --orange:#ff8a00;
  --orange-deep:#ff7a00;
  --teal-sub:#1f83a7;
  --teal-top:#2693b9;
  --teal-line:#3aa3c7;
  --page:#ececec;
  --card:#ffffff;
  --card-head:#f7f7f7;
  --border:#d8d8d8;
  --text:#4a4a4a;
  --muted:#777;
  --link:#1f7fa6;
  --white:#ffffff;
  --mark:#1a1a1a;
}
*{box-sizing:border-box;margin:0;padding:0}
html,body{width:1200px;height:881px;overflow:hidden}
body{position:relative;background:var(--page);font-family:'Mulish',Arial,sans-serif;color:var(--text)}
.header{position:absolute;left:0;top:0;width:1200px;height:125px;background:var(--header)}
.brand{position:absolute;left:60px;top:40px;display:flex;align-items:center;gap:12px;color:var(--white);font-size:24px;font-weight:500;line-height:1}
.brand-dot{width:44px;height:44px;border-radius:50%;background:var(--mark)}
.search{position:absolute;left:356px;top:43px;width:487px;height:40px;border:1px solid #9a9a9a;border-radius:2px;display:flex;align-items:center;padding-left:12px;color:#cfcfcf;font-size:14px;gap:10px}
.user{position:absolute;left:898px;top:39px;display:flex;align-items:center;gap:8px;color:var(--white);font-size:15px;font-weight:500}
.avatar{border-radius:50%;background:linear-gradient(135deg,#b9a393,#6d5a50);border:2px solid #fff}
.user .avatar{width:46px;height:46px}
.sidebar{position:absolute;left:0;top:125px;width:359px;height:698px;background:var(--teal-top)}
.shared{height:53px;background:linear-gradient(180deg,#ff9410,var(--orange-deep));display:flex;align-items:center;padding-left:62px;gap:8px;color:var(--white);font-size:18.5px}
.kit{background:var(--teal-sub);height:394px}
.kit-head{height:58px;display:flex;align-items:center;padding-left:64px;gap:8px;color:var(--white);font-size:18.5px;position:relative}
.kit-head .chev{position:absolute;right:24px;top:22px}
.sub{height:47px;border-bottom:1px solid var(--teal-line);display:flex;align-items:center;color:var(--white);font-size:15px}
.sub:last-child{border-bottom:none}
.sub .ico{width:113px;display:flex;justify-content:flex-end;padding-right:10px}
.top-item{height:62px;display:flex;align-items:center;padding-left:58px;gap:10px;color:var(--white);font-size:18.5px;border-bottom:2px solid #d5ecf4}
.top-item:last-child{border-bottom:none}
.notes-select{position:absolute;left:897px;top:152px;width:175px;height:37px;background:#f3f3f3;border:1px solid var(--border);display:flex;align-items:center;justify-content:space-between;padding:0 12px;font-size:14px;color:#666}
.card{position:absolute;left:401px;top:206px;width:670px;height:568px;background:var(--card);border:1px solid var(--border)}
.card-head{height:66px;background:var(--card-head);border-bottom:1px solid var(--border);display:flex;align-items:center;padding-left:20px;gap:13px}
.card-head .avatar{width:41px;height:41px;border:none}
.author{color:var(--link);font-size:15px;font-weight:500}
.stamp{color:var(--muted);font-size:13px;margin-top:3px}
.card-body{padding:27px 34px 0}
.title{font-size:16.5px;font-weight:500;color:#4a4a4a;margin-bottom:16px}
.card-body p{font-size:12.4px;line-height:20.6px;color:#555;margin-bottom:20.6px}
.actions{position:absolute;left:33px;top:376px;display:flex;gap:8px}
.btn{width:117px;height:34px;border:2px solid;border-radius:2px;display:flex;align-items:center;justify-content:center;font-size:14px;background:#fff}
.btn-more{border-color:var(--link);color:var(--link)}
.btn-close{border-color:var(--orange);color:var(--orange)}
.composer{position:absolute;left:16px;top:513px;width:641px;height:40px;background:#efefef;border:1px solid var(--border);display:flex;align-items:center;padding-left:21px;font-size:13px;color:#888}
.tools{position:absolute;right:17px;top:4px;display:flex;gap:8px}
.tool{width:29px;height:29px;border-radius:50%;background:var(--orange);display:flex;align-items:center;justify-content:center}
.footer{position:absolute;left:0;top:823px;width:1200px;height:58px;background:var(--footer);color:#d6d6d6;font-size:13.5px;display:flex;align-items:center;padding-left:450px}
</style>
</head>
<body>
<header class="header">
  <div class="brand"><span class="brand-dot"></span>TallyNest</div>
  <div class="search">
    <svg width="17" height="17" viewBox="0 0 20 20"><circle cx="8" cy="8" r="6" fill="none" stroke="#cfcfcf" stroke-width="2.4"/><line x1="12.5" y1="12.5" x2="18" y2="18" stroke="#cfcfcf" stroke-width="2.6" stroke-linecap="round"/></svg>
    Enter Keyword
  </div>
  <div class="user">
    <div class="avatar" role="img" aria-label="Profile photo of Nora Fenwick"></div>
    Nora Fenwick
  </div>
</header>

<nav class="sidebar">
  <div class="shared">
    <svg width="30" height="32" viewBox="0 0 30 32" fill="none" stroke="#fff" stroke-width="2.2"><path d="M10 12H3v18h24V12h-7"/><path d="M15 22V3M9 9l6-6 6 6"/></svg>
    Current Shared Project
  </div>
  <div class="kit">
    <div class="kit-head">
      <svg width="22" height="22" viewBox="0 0 22 22"><circle cx="11" cy="11" r="11" fill="#fff"/><path d="M6 11.5l3.5 3.5L16 8" fill="none" stroke="#1f83a7" stroke-width="2.6"/></svg>
      Startup Starter Kit
      <svg class="chev" width="20" height="12" viewBox="0 0 20 12"><path d="M1 1l9 9 9-9" fill="none" stroke="#fff" stroke-width="2"/></svg>
    </div>
    <div class="sub"><span class="ico"><svg width="18" height="18" viewBox="0 0 18 18"><path d="M2 16l1-4L13 2l3 3L6 15z" fill="#d6ecf4"/></svg></span>Meeting Notes/ Business SCRUM</div>
    <div class="sub"><span class="ico"><svg width="22" height="18" viewBox="0 0 22 18"><rect x="1" y="4" width="20" height="13" rx="2" fill="#d6ecf4"/><rect x="7" y="1" width="8" height="4" fill="none" stroke="#d6ecf4" stroke-width="2"/><rect x="9" y="9" width="4" height="3" fill="#1f83a7"/></svg></span>Corporate Structure</div>
    <div class="sub"><span class="ico"><svg width="28" height="20" viewBox="0 0 28 20" fill="none" stroke="#d6ecf4" stroke-width="1.6"><ellipse cx="7" cy="7" rx="6" ry="2.5"/><path d="M1 7v10c0 1.4 2.7 2.5 6 2.5s6-1.1 6-2.5V7M1 12c0 1.4 2.7 2.5 6 2.5s6-1.1 6-2.5"/><ellipse cx="21" cy="3" rx="6" ry="2.2"/><path d="M15 3v14c0 1.4 2.7 2.5 6 2.5s6-1.1 6-2.5V3M15 8c0 1.4 2.7 2.5 6 2.5s6-1.1 6-2.5M15 13c0 1.4 2.7 2.5 6 2.5s6-1.1 6-2.5"/></svg></span>Fund Raising / Crop Dev</div>
    <div class="sub"><span class="ico"><svg width="14" height="26" viewBox="0 0 14 26"><text x="7" y="21" text-anchor="middle" font-size="24" fill="#d6ecf4" font-family="Mulish,sans-serif">$</text></svg></span>Operating Finance</div>
    <div class="sub"><span class="ico"><svg width="24" height="20" viewBox="0 0 24 20" fill="none" stroke="#d6ecf4" stroke-width="1.8"><path d="M1 1v18h22"/><path d="M4 15l5-6 4 3 7-7"/></svg></span>Sales / Business Development</div>
    <div class="sub"><span class="ico"><svg width="22" height="22" viewBox="0 0 22 22"><path d="M21 1c-7 0-11 4-13 8l-4 1-3 4 5-1 3 3-1 5 4-3 1-4c4-2 8-6 8-13z" fill="#d6ecf4"/></svg></span>Marketing</div>
    <div class="sub"><span class="ico"><svg width="22" height="22" viewBox="0 0 22 22"><path d="M2 6h5a3 3 0 1 1 5 0h5v5a3 3 0 1 1 0 5v5H12a3 3 0 1 0-5 0H2z" fill="#d6ecf4"/></svg></span>Other</div>
  </div>
  <div class="top-item">
    <svg width="28" height="26" viewBox="0 0 28 26" fill="#fff"><rect x="11" y="0" width="6" height="6"/><rect x="13" y="6" width="2" height="5"/><rect x="3" y="11" width="22" height="2"/><rect x="3" y="11" width="2" height="6"/><rect x="23" y="11" width="2" height="6"/><rect x="13" y="11" width="2" height="6"/><rect x="0" y="17" width="7" height="8"/><rect x="10.5" y="17" width="7" height="8"/><rect x="21" y="17" width="7" height="8"/></svg>
    TallyNest Top Project Picks
  </div>
  <div class="top-item">
    <svg width="28" height="27" viewBox="0 0 28 27"><path d="M14 1l3.8 8.3 9 .9-6.8 6.1 2 8.9L14 20.6 6 25.2l2-8.9L1.2 10.2l9-.9z" fill="none" stroke="#fff" stroke-width="1.6"/></svg>
    Most Popular Public Projects
  </div>
  <div class="top-item">
    <svg width="30" height="24" viewBox="0 0 30 24" fill="#fff"><circle cx="15" cy="6" r="5"/><circle cx="5.5" cy="7" r="3.5"/><circle cx="24.5" cy="7" r="3.5"/><path d="M7 23c0-6 3.5-10 8-10s8 4 8 10z"/><path d="M0 19c0-4 2.5-7 6-7 1 0 2 .3 2.5.7C7 14.8 6 17 6 19z"/><path d="M30 19c0-4-2.5-7-6-7-1 0-2 .3-2.5.7 1.5 2.1 2.5 4.3 2.5 6.3z"/></svg>
    All Public Projects
  </div>
</nav>

<div class="notes-select">Notes
  <svg width="14" height="8" viewBox="0 0 14 8"><path d="M1 1l6 6 6-6" fill="none" stroke="#777" stroke-width="1.6"/></svg>
</div>

<article class="card">
  <div class="card-head">
    <div class="avatar" role="img" aria-label="Profile photo of Dorian Keyle"></div>
    <div>
      <div class="author">Dorian Keyle TN Cases</div>
      <div class="stamp">6/1/2017&nbsp; 6:63 am IST</div>
    </div>
  </div>
  <div class="card-body">
    <h2 class="title">Welcome to the TallyNest 'Startup Starter Kit' - do more better!</h2>
    <p>We the team at TallyNest have been used the assets and structure in this kit across several startups. Most of what you will find here are things that will help you get started in your earliest phases.</p>
    <p>We recommend you look though the structure of this project as a an organizational logic, and then dig into some of the documentation templates.</p>
    <p>Best of luck on your venture, and please let us know if we can help!</p>
    <p>TMP - General Business Scrum Template<br>https://docs.orvane.example/document/d/7kRzWqLmTb2NcYpe5Vd8Hs0GjXu4Af9QnEo3KiTlMrBy/edit</p>
  </div>
  <div class="actions">
    <div class="btn btn-more">View More</div>
    <div class="btn btn-close">Close</div>
  </div>
  <div class="composer">Type here
    <div class="tools">
      <span class="tool"><svg width="18" height="16" viewBox="0 0 18 16" fill="none" stroke="#fff" stroke-width="1.6"><ellipse cx="7" cy="6" rx="6" ry="4.5"/><path d="M3 9.5L2 13l4-2.5"/><path d="M13 4.5c2.5.6 4 2.2 4 4 0 1.2-.6 2.2-1.6 3l.6 3-3-1.8"/></svg></span>
      <span class="tool"><svg width="16" height="16" viewBox="0 0 16 16" fill="none" stroke="#fff" stroke-width="1.8"><path d="M7 9l2-2"/><path d="M6 6l3-3a2.5 2.5 0 0 1 3.5 3.5l-3 3"/><path d="M10 10l-3 3a2.5 2.5 0 0 1-3.5-3.5l3-3"/></svg></span>
      <span class="tool"><svg width="16" height="14" viewBox="0 0 16 14"><path d="M1 4h3l1.5-2.5h5L12 4h3v9H1z" fill="#fff"/><circle cx="8" cy="8.3" r="2.8" fill="#ff8a00"/></svg></span>
      <span class="tool"><svg width="16" height="16" viewBox="0 0 16 16" fill="none" stroke="#fff" stroke-width="1.6"><path d="M9 2H2v12h12V7"/><path d="M6 10l1-3 7-6 2 2-7 6z"/></svg></span>
    </div>
  </div>
</article>

<footer class="footer">© 2017 Company Name&nbsp; All right reserved</footer>
</body>
</html>
```